Simple and Clean business card design

We would like the design to be simple clean and to incorporate our colors.

We are open to your design and talent, we have the dots in our logo as we think of it as data points and we connect data points for people.

We are open to see the great creative and clean design you bring to the table

Contact Information for Business Card

please include: name, position, email, phone and website

Font styles to use
Sans Serif

Requirements
Must have
• my colors incorporated, simplicity
Nice to have
• lots of white space, simplicity
Should not have
• complexicity/ complex art

```html
<!DOCTYPE html>
<html lang="en">
<head>
<meta charset="utf-8">
<title>Sorrel — Business Card</title>
<link rel="stylesheet" href="https://fonts.googleapis.com/css2?family=Open+Sans:wght@400;600&family=Saira:wght@600&display=swap">
<style>
  :root {
    --brand-blue: #4285f4;
    --ink: #111111;
    --text-dark: #222222;
    --paper: #ffffff;
    --page: #fdfdfd;
    --card-edge: #1a1a1a;
  }
  * { margin: 0; padding: 0; box-sizing: border-box; }
  html, body {
    width: 1200px; height: 1200px; overflow: hidden;
    background: var(--page);
    font-family: "Open Sans", Arial, sans-serif;
  }
  .canvas { position: relative; width: 1200px; height: 1200px; }
  .card {
    position: absolute; left: 216px; width: 775px; height: 430px;
    border: 1px solid var(--card-edge);
  }
  .card--front { top: 147px; background: var(--brand-blue); }
  .card--back { top: 630px; background: var(--paper); }

  .wordmark {
    position: absolute; display: flex; align-items: center; gap: 14px;
    font-family: "Open Sans", Arial, sans-serif; font-weight: 600;
    line-height: 1; letter-spacing: 1px;
  }
  .wordmark__dot { border-radius: 50%; flex: none; }

  .card--front .wordmark {
    left: 50%; top: 228px; transform: translate(-50%, -50%);
    font-size: 124px; color: var(--paper);
  }
  .card--front .wordmark__dot { width: 30px; height: 30px; background: var(--paper); }

  .front-url {
    position: absolute; left: 0; right: 0; top: 359px; transform: translateY(-50%);
    display: flex; justify-content: center; align-items: center; gap: 34px;
    color: var(--paper); font-size: 19px;
  }
  .front-url__rule { width: 104px; height: 2px; background: var(--paper); }

  .card--back .wordmark {
    left: 64px; top: 222px; transform: translateY(-50%);
    font-size: 98px; color: var(--ink);
  }
  .card--back .wordmark__dot { width: 24px; height: 24px; background: var(--brand-blue); }

  .divider {
    position: absolute; left: 390px; top: 114px; width: 3px; height: 203px;
    background: var(--brand-blue);
  }
  .contact-block { position: absolute; left: 430px; top: 108px; }
  .person-name {
    font-family: "Saira", Arial, sans-serif; font-weight: 600;
    font-size: 34px; line-height: 1; color: var(--brand-blue); letter-spacing: 1px;
  }
  .person-role {
    margin-top: 4px; font-family: "Saira", Arial, sans-serif; font-weight: 600;
    font-size: 15px; letter-spacing: 2px; color: var(--text-dark);
  }
  .contact-list { list-style: none; margin-top: 14px; }
  .contact-item { display: flex; align-items: center; height: 34px; margin-bottom: 16px; }
  .contact-icon {
    width: 34px; height: 34px; border-radius: 5px; background: var(--brand-blue);
    display: flex; align-items: center; justify-content: center; flex: none;
  }
  .contact-text { margin-left: 19px; font-size: 21px; color: var(--text-dark); }
</style>
</head>
<body>
<main class="canvas">
  <section class="card card--front">
    <div class="wordmark"><span class="wordmark__text">Sorrel</span><span class="wordmark__dot"></span></div>
    <div class="front-url">
      <span class="front-url__rule"></span>
      <span class="front-url__text">www.sorrel.one</span>
      <span class="front-url__rule"></span>
    </div>
  </section>

  <section class="card card--back">
    <div class="wordmark"><span class="wordmark__text">Sorrel</span><span class="wordmark__dot"></span></div>
    <div class="divider"></div>
    <div class="contact-block">
      <h1 class="person-name">MARTIN VALE</h1>
      <p class="person-role">FOUNDER</p>
      <ul class="contact-list">
        <li class="contact-item">
          <span class="contact-icon">
            <svg width="20" height="20" viewBox="0 0 24 24" fill="#fff" aria-hidden="true"><path d="M6.6 10.8a15.1 15.1 0 0 0 6.6 6.6l2.2-2.2a1 1 0 0 1 1-.25 11.4 11.4 0 0 0 3.6.57 1 1 0 0 1 1 1V20a1 1 0 0 1-1 1A17 17 0 0 1 3 4a1 1 0 0 1 1-1h3.5a1 1 0 0 1 1 1c0 1.25.2 2.45.57 3.57a1 1 0 0 1-.25 1z"/></svg>
          </span>
          <span class="contact-text">555-201-3847</span>
        </li>
        <li class="contact-item">
          <span class="contact-icon">
            <svg width="22" height="16" viewBox="0 0 22 16" fill="none" stroke="#fff" stroke-width="1.4" aria-hidden="true"><rect x="1" y="1" width="20" height="14"/><path d="M1 1l10 8 10-8M1 15l7-6M21 15l-7-6"/></svg>
          </span>
          <span class="contact-text">martin.vale@sorrel.one</span>
        </li>
        <li class="contact-item">
          <span class="contact-icon">
            <svg width="22" height="22" viewBox="0 0 24 24" fill="none" stroke="#fff" stroke-width="1.3" aria-hidden="true"><circle cx="12" cy="12" r="10"/><ellipse cx="12" cy="12" rx="4.5" ry="10"/><path d="M2 12h20M4 6.5h16M4 17.5h16M12 2v20"/></svg>
          </span>
          <span class="contact-text">www.sorrel.one</span>
        </li>
      </ul>
    </div>
  </section>
</main>
</body>
</html>
```